KBT Business Cards

We require business cards for our business. We would like a matte black back to the card, with our logo centred in the middle. The front side of the card is open to design.

Target Market(s)

Clients looking for legal services (professional)

Industry/Entity Type

Legal

Contact Information for Business Card

Doran Kelbrath
Partner
Mobile: 0461 738 524
Email: doran@kbtlaw.co
Website: www.kbtlaw.co
Level 3, 118 Wendmore Street
Sydney NSW 2000

Font styles to use
Other font styles liked:
• Avenir

Colors
f04a50
ffffff
1b1b1b

Requirements
Must have
• Black back with logo included in the centre of the card.
• Our font is Avenir.

```html
<!DOCTYPE html>
<html lang="en">
<head>
<meta charset="utf-8">
<title>KBT Business Cards</title>
<link rel="stylesheet" href="https://fonts.googleapis.com/css2?family=Nunito+Sans:wght@400;600;700&display=swap">
<style>
  :root {
    --accent: #e0264f;
    --white: #ffffff;
    --card: #1b1b1b;
    --card-deep: #111111;
    --muted: #d8d8d8;
    --rule: #7a7a7a;
    --stage: #d3d4d6;
  }
  * { margin: 0; padding: 0; box-sizing: border-box; }
  html, body {
    width: 1106px;
    height: 1200px;
    overflow: hidden;
    background: var(--stage);
    font-family: "Nunito Sans", sans-serif;
  }
  .card {
    position: absolute;
    left: 138px;
    width: 835px;
    height: 476px;
    background: radial-gradient(ellipse at 45% 20%, #242424 0%, var(--card) 45%, var(--card-deep) 100%);
    overflow: hidden;
  }
  .card--front { top: 93px; }
  .card--back { top: 617px; }

  /* Firm name */
  .firm {
    position: absolute;
    display: flex;
    align-items: center;
  }
  .firm__square {
    background: var(--accent);
    flex: none;
  }
  .firm__name {
    color: var(--white);
    font-weight: 700;
    text-transform: uppercase;
    line-height: 1.1;
  }
  .card--front .firm { left: 100px; top: 196px; gap: 22px; }
  .card--front .firm__square { width: 46px; height: 46px; }
  .card--front .firm__name { font-size: 30px; }

  .card--back .firm { left: 170px; top: 86px; gap: 44px; }
  .card--back .firm__square { width: 78px; height: 78px; }
  .card--back .firm__name { font-size: 47px; }

  /* Front details */
  .divider {
    position: absolute;
    left: 425px;
    top: 106px;
    width: 1px;
    height: 264px;
    background: var(--rule);
  }
  .details {
    position: absolute;
    left: 460px;
    top: 104px;
    color: var(--muted);
  }
  .details__name {
    color: var(--accent);
    font-size: 27px;
    font-weight: 700;
    letter-spacing: 0.3px;
    text-transform: uppercase;
    line-height: 1.1;
  }
  .details__role {
    font-size: 20px;
    text-transform: uppercase;
    letter-spacing: 0.5px;
    line-height: 1.3;
  }
  .details__address {
    margin-top: 20px;
    font-size: 21px;
    line-height: 32px;
    font-style: normal;
  }
  .contacts {
    list-style: none;
    margin-top: 20px;
  }
  .contacts__item {
    display: flex;
    align-items: center;
    gap: 10px;
    font-size: 21px;
    height: 35px;
  }
  .contacts__icon { width: 22px; height: 22px; flex: none; }

  /* Back website */
  .site {
    position: absolute;
    left: 0;
    right: 0;
    top: 392px;
    text-align: center;
    color: var(--white);
    font-size: 21px;
    letter-spacing: 4.5px;
  }
  .site__domain { color: var(--accent); font-weight: 700; }
</style>
</head>
<body>

<section class="card card--front" aria-label="Business card front">
  <div class="firm">
    <span class="firm__square" aria-hidden="true"></span>
    <p class="firm__name">Kelbrath<br>Brant<br>Legal</p>
  </div>

  <div class="divider" aria-hidden="true"></div>

  <div class="details">
    <h1 class="details__name">Doran Kelbrath</h1>
    <p class="details__role">Partner</p>
    <address class="details__address">Level 3, 118 Wendmore Street<br>Sydney NSW 2000</address>
    <ul class="contacts">
      <li class="contacts__item">
        <svg class="contacts__icon" viewBox="0 0 22 22" aria-hidden="true">
          <circle cx="11" cy="11" r="9.5" fill="none" stroke="var(--accent)" stroke-width="1.5"/>
          <rect x="7.5" y="5" width="7" height="12" rx="1.3" fill="none" stroke="var(--accent)" stroke-width="1.5"/>
          <line x1="10" y1="14.5" x2="12" y2="14.5" stroke="var(--accent)" stroke-width="1.3"/>
        </svg>
        0461 738 524
      </li>
      <li class="contacts__item">
        <svg class="contacts__icon" viewBox="0 0 22 22" aria-hidden="true">
          <rect x="2" y="5" width="18" height="12" fill="var(--accent)"/>
          <polyline points="2,5 11,12 20,5" fill="none" stroke="var(--card)" stroke-width="1.4"/>
        </svg>
        doran@kbtlaw.co
      </li>
      <li class="contacts__item">
        <svg class="contacts__icon" viewBox="0 0 22 22" aria-hidden="true">
          <g fill="none" stroke="var(--accent)" stroke-width="1.5">
            <circle cx="11" cy="11" r="9"/>
            <ellipse cx="11" cy="11" rx="4" ry="9"/>
            <line x1="2" y1="11" x2="20" y2="11"/>
            <path d="M4 6.5h14M4 15.5h14"/>
          </g>
        </svg>
        www.kbtlaw.co
      </li>
    </ul>
  </div>
</section>

<section class="card card--back" aria-label="Business card back">
  <div class="firm">
    <span class="firm__square" aria-hidden="true"></span>
    <p class="firm__name">Kelbrath<br>Brant<br>Legal</p>
  </div>
  <p class="site">www.<span class="site__domain">kbtlaw</span>.co</p>
</section>

</body>
</html>
```